Wix Design for a Clothing Design Web Marketing Site

We need a Wix design and content (including any images and copy) for a clothing design web storefront, Sew To Suit (or sewtosuit). Rough ideas and content can be found at http://marenvoltis.wix.com/sewtosuit.

Sew To Suit is an innovative business concept that combines fashion and entertainment. The business model allows customers to actively participate in the creation of fashion designs/concepts , visualize the garment in the customer’s body in 3D, and buy the physical garment made specially to fit the customer.
The fashion consultant will be able to create the design based on client's desires and test various possibilities (size, fabric, cut, etc..) in front of the customer, using software Drapova (the software is a key component of this business model)
(when developing the website use images from Drapova)
After the design is created, the customer can choose to order the actual piece. The garment will be made according to the created design, the customer measurements.

Target Market(s)

Primarily women from 25 to 45, who are fashion enthusiasts and appreciate fit and exclusivity. They are hedonistic shoppers, who shop for entertainment.
Men (metrosexuals) who are fashion enthusiasts, also hedonistic shoppers.

Industry/Entity Type

Clothing

Font styles to use
Serif
Sans Serif

Requirements
Must have
• Must have a landing page (home) or section, that gives the consumer an idea of what Sew To Suit will do for them, an about page or section that tells about the company and product, a how it works page or section that describes how it works (http://marenvoltis.wix.com/sewtosuit#!services3/c192y), and page or section about pricing, and a page or section on how to contact us.
Nice to have
• Very modern and clean. The website must be based on the main picture of the studio in the example. If that studio is the store, what will the website look like?
• Colors yellow, grey and white. Use the zig zag in yellow and white. You can change the size of the lines. The zig zagi gives the modern and bold accent. Outfits in pictures must show nicely tailored garments.

```html
<!DOCTYPE html>
<html lang="en">
<head>
<meta charset="utf-8">
<title>Sew To Suit — Contact Us</title>
<link rel="stylesheet" href="https://fonts.googleapis.com/css2?family=Italiana&family=Open+Sans:wght@400;600&family=Roboto+Condensed:wght@400;700&family=Roboto+Slab:wght@300;400;700&display=swap">
<style>
  :root {
    --yellow: #f7e93a;
    --yellow-soft: #fbe873;
    --zig-white: #fbeef0;
    --ink: #1c1c1c;
    --charcoal: #262626;
    --charcoal-deep: #1a1a1a;
    --nav-grey: #6a737c;
    --text: #333333;
    --muted: #7a7a7a;
    --footer-head: #8d96a0;
    --white: #ffffff;
    --field-line: #8a8a8a;
  }
  * { box-sizing: border-box; margin: 0; padding: 0; }
  html, body { width: 1166px; height: 1200px; overflow: hidden; }
  body { position: relative; background: var(--white); font-family: "Open Sans", sans-serif; color: var(--text); }

  .site-header { position: absolute; left: 0; top: 0; width: 1166px; height: 183px; }
  .header-shape { position: absolute; inset: 0; }
  .brand { position: absolute; left: 66px; top: 14px; width: 284px; height: 160px; }
  .brand-disc { position: absolute; left: 72px; top: 0; width: 142px; height: 142px; border-radius: 50%; background: var(--yellow-soft); border: 5px solid var(--white); box-shadow: 0 0 0 1px #ddd; }
  .brand-name { position: absolute; left: 0; top: 117px; width: 284px; height: 42px; background: var(--white); border: 1px solid #ddd; font-family: "Roboto Slab", serif; font-weight: 700; font-size: 30px; line-height: 40px; text-align: center; color: var(--ink); letter-spacing: 1px; }
  .tagline { position: absolute; left: 540px; top: 40px; font-family: "Italiana", serif; font-size: 49px; line-height: 48px; color: var(--white); }

  .main-nav { position: absolute; left: 0; top: 183px; width: 1166px; height: 41px; background: var(--nav-grey); display: flex; padding-left: 69px; }
  .main-nav a { font-family: "Roboto Condensed", sans-serif; font-size: 17px; color: var(--white); text-decoration: none; line-height: 41px; padding: 0 20px; margin-right: 15px; }
  .main-nav a.is-current { background: var(--charcoal-deep); padding: 0 35px; margin-left: -8px; }

  .page-banner { position: absolute; left: 0; top: 224px; width: 1166px; height: 128px; background: linear-gradient(135deg, #2b2b2b, #1e1e1e 60%, #2a2a2a); }
  .page-banner h1 { font-family: "Roboto Slab", serif; font-weight: 400; font-size: 31px; color: var(--yellow); text-align: center; line-height: 128px; }

  .zigzag-field { position: absolute; left: 0; top: 352px; width: 1166px; height: 582px; background: linear-gradient(90deg, var(--yellow-soft) 0%, var(--zig-white) 3%, var(--yellow-soft) 6%, var(--yellow-soft) 94%, var(--zig-white) 97%, var(--yellow-soft) 100%); }

  .contact-panel { position: absolute; left: 65px; top: 352px; width: 1008px; height: 593px; background: var(--white); }
  .panel-title { position: absolute; top: 24px; width: 100%; text-align: center; font-family: "Roboto Slab", serif; font-weight: 300; font-size: 27px; color: var(--ink); }
  .divider { position: absolute; left: 326px; top: 74px; }
  .intro { position: absolute; left: 70px; top: 128px; width: 868px; text-align: center; font-size: 14.5px; line-height: 21px; color: var(--text); }

  .contact-form { position: absolute; left: 58px; top: 225px; width: 405px; }
  .field { display: block; width: 405px; height: 43px; border: 1px solid var(--field-line); margin-bottom: 10px; font-family: "Open Sans", sans-serif; font-size: 12.5px; color: var(--muted); padding: 10px 15px; }
  .field-message { height: 130px; }
  .btn { display: inline-block; background: var(--yellow); font-family: "Roboto Condensed", sans-serif; font-size: 15px; color: var(--ink); text-align: center; text-transform: uppercase; border: 0; }
  .btn-send { width: 110px; height: 43px; line-height: 43px; margin-top: 0; }

  .side-block { position: absolute; left: 545px; width: 420px; }
  .side-heading { font-family: "Roboto Condensed", sans-serif; font-weight: 700; font-size: 13.5px; color: var(--ink); padding-bottom: 10px; border-bottom: 1px dashed #777; }
  .social { display: flex; gap: 8px; margin-top: 23px; padding-left: 5px; }
  .social span { width: 41px; height: 41px; border-radius: 50%; background: var(--yellow); }
  .map-area { margin-top: 14px; width: 420px; height: 113px; background: linear-gradient(135deg, #8d8d8d, #6c6c6c); position: relative; }
  .map-pin { position: absolute; left: 164px; top: 10px; }
  .map-address { position: absolute; width: 100%; top: 40px; left: -30px; text-align: center; font-family: "Open Sans", sans-serif; font-weight: 600; font-size: 12px; line-height: 15px; color: var(--white); }

  .site-footer { position: absolute; left: 0; top: 934px; width: 1166px; height: 213px; background: var(--charcoal); }
  .footer-col { position: absolute; top: 48px; }
  .footer-col h3 { font-family: "Roboto Condensed", sans-serif; font-weight: 400; font-size: 15px; color: var(--footer-head); text-transform: uppercase; margin-bottom: 8px; }
  .footer-col p, .footer-col li { font-size: 12.5px; line-height: 20.6px; color: #e6e6e6; list-style: none; }
  .footer-col ul { padding-left: 3px; }
  .accent { color: var(--yellow); }
  .newsletter-field { width: 245px; height: 35px; background: var(--white); font-family: "Roboto Condensed", sans-serif; font-size: 12px; color: #999; padding: 10px; margin-top: 10px; }
  .btn-submit { width: 98px; height: 35px; line-height: 35px; margin-top: 10px; font-size: 14.5px; }
  .footer-brand { position: absolute; left: 852px; top: 50px; width: 206px; height: 118px; }
  .footer-brand-disc { position: absolute; left: 51px; top: 0; width: 106px; height: 106px; border-radius: 50%; background: #6b6a3c; border: 3px solid #777; }
  .footer-brand-name { position: absolute; left: 0; top: 83px; width: 206px; height: 29px; background: #7b7520; font-family: "Roboto Slab", serif; font-weight: 700; font-size: 20px; line-height: 29px; text-align: center; color: var(--ink); }

  .legal-bar { position: absolute; left: 0; top: 1147px; width: 1166px; height: 53px; background: #121212; text-align: center; font-size: 11.5px; line-height: 53px; color: #e6e6e6; }
</style>
</head>
<body>

<header class="site-header">
  <svg class="header-shape" width="1166" height="183" viewBox="0 0 1166 183" aria-hidden="true">
    <rect width="1166" height="183" fill="#ffffff"/>
    <polygon points="533,0 1166,0 1166,183 455,183" fill="#262626"/>
  </svg>
  <div class="brand">
    <div class="brand-disc"></div>
    <div class="brand-name">SEW TO SUIT</div>
  </div>
  <p class="tagline">Clothes made specially for<br>You and designed by you</p>
</header>

<nav class="main-nav">
  <a href="#">Home</a>
  <a href="#">What is Sew To Suit?</a>
  <a href="#">How It Works?</a>
  <a href="#">Price</a>
  <a href="#" class="is-current">Contact Us</a>
</nav>

<section class="page-banner"><h1>Contact Us</h1></section>

<div class="zigzag-field" role="img" aria-label="Yellow and white zigzag pattern background"></div>

<main class="contact-panel">
  <h2 class="panel-title">For Any Queries Mail Us</h2>
  <svg class="divider" width="356" height="26" viewBox="0 0 356 26" aria-hidden="true">
    <line x1="0" y1="13" x2="158" y2="13" stroke="#333" stroke-dasharray="2 1"/>
    <line x1="198" y1="13" x2="356" y2="13" stroke="#333" stroke-dasharray="2 1"/>
    <polygon points="178,1 190,13 178,25 166,13" fill="#1c1c1c"/>
  </svg>
  <p class="intro">To schedule an appointment, contact us at studio@sewtosuit.com or you can fill up the form and sent to us. One of our executive will contact you within 24 business hours after the mail receive.</p>

  <form class="contact-form">
    <div class="field">Your name</div>
    <div class="field">Your email id</div>
    <div class="field">Your phone no</div>
    <div class="field field-message">Your message</div>
    <div class="btn btn-send">Send</div>
  </form>

  <div class="side-block" style="top:226px">
    <h3 class="side-heading">GET IN TOUCH WITH US</h3>
    <div class="social"><span></span><span></span><span></span></div>
  </div>
  <div class="side-block" style="top:355px">
    <h3 class="side-heading">GET DIRECTION</h3>
    <div class="map-area" role="img" aria-label="Street map of the studio location in Glasgow">
      <svg class="map-pin" width="22" height="28" viewBox="0 0 22 28" aria-hidden="true">
        <path d="M11 27 C4 18 1 14 1 10 a10 10 0 0 1 20 0 c0 4 -3 8 -10 17z" fill="#e84b4b"/>
        <circle cx="11" cy="10" r="5" fill="#fff"/>
      </svg>
      <p class="map-address">14 Thimble Lane Glasgow<br>G12 8QT</p>
    </div>
  </div>
</main>

<footer class="site-footer">
  <div class="footer-col" style="left:100px">
    <h3>Quick Links</h3>
    <ul>
      <li>Home</li>
      <li>What is Sew To Suit?</li>
      <li>How It Works?</li>
      <li>Price</li>
      <li>Contact Us</li>
    </ul>
  </div>
  <div class="footer-col" style="left:301px">
    <h3>Company Info</h3>
    <p>48 Hemline Ave,<br>1st Floor, Room No 210<br>Los Angeles, CA<br>USA<br>Ph: <span class="accent">555 0142 318</span><br>Email: <span class="accent">info@whatissewtosuit</span></p>
  </div>
  <div class="footer-col" style="left:571px">
    <h3>Subscribe Newsletter</h3>
    <div class="newsletter-field">Type your email id</div>
    <div class="btn btn-submit">Submit</div>
  </div>
  <div class="footer-brand">
    <div class="footer-brand-disc"></div>
    <div class="footer-brand-name">SEW TO SUIT</div>
  </div>
</footer>

<div class="legal-bar">© 2015, All Rights Reserved, Sew To Suit</div>

</body>
</html>
```